UI/ UX Design for ERP Software

We need a new UX/UI interface for a ERP software for property managers. Our CMMS / ERP solution is made based on responsive design technologies and is coded in PHP.
The overall UX to be similar to Tev Ulna - easy navigation, intuitive menus.

Industry/Entity Type

Property Management

Number of Pages Required

5+ page

Requirements
Must have
• Round dock buttons
Consistent icons across the application
Enough Spacing between buttons/icons/ menu
Consistent Font
Nice to have
• We would like the UX to allow the users to use the application without /minimum training.
Should not have
• we don't want anything that is classic with respect to UX

```html
<!DOCTYPE html>
<html lang="en">
<head>
<meta charset="utf-8">
<title>Domiva – Active Dashboard</title>
<link href="https://fonts.googleapis.com/css2?family=Roboto:wght@400;500&display=swap" rel="stylesheet">
<style>
:root{
  --blue:#0a7cff;
  --ink:#222;
  --rail:#f0f0f0;
  --card-border:#e4e4e4;
  --btn-grey:#cfcfcf;
  --grid:#e6e6e6;
}
*{box-sizing:border-box;margin:0;padding:0}
html,body{width:1200px;height:945px;overflow:hidden;background:#fff;font-family:'Roboto',sans-serif;color:var(--ink)}
.canvas{position:relative;width:1200px;height:945px;overflow:hidden}
.topbar{position:absolute;left:0;top:0;width:1200px;height:74px;background:var(--blue)}
.brand{position:absolute;left:20px;top:20px;color:#fff;font-size:32px;font-weight:500;display:flex;align-items:center;gap:8px;line-height:34px}
.brand-dot{width:22px;height:22px;border-radius:50%;background:#fff}
.nav{position:absolute;top:21px;height:32px;line-height:30px;color:#fff;font-size:10.5px;white-space:nowrap}
.nav.active{border:1px solid #fff;padding:0 5px}
.avatar{position:absolute;left:1051px;top:18px;width:38px;height:38px;border-radius:50%;background:linear-gradient(135deg,#cfd8e3,#d64a3a)}
.user{position:absolute;left:1096px;top:29px;color:#fff;font-size:11.5px;white-space:nowrap}
.rail{position:absolute;left:0;top:74px;width:73px;height:871px;background:var(--rail)}
.dock{position:absolute;left:17px;width:28px;height:28px;border-radius:50%;border:1px solid #888;background:#fff;display:flex;align-items:center;justify-content:center}
.back{position:absolute;left:14px;top:822px;width:40px;height:40px;border-radius:50%;background:var(--blue);display:flex;align-items:center;justify-content:center}
.stat{position:absolute;top:106px;height:67px;border:1px solid var(--card-border);box-shadow:0 1px 3px rgba(0,0,0,.08);background:#fff;padding:13px 13px;white-space:nowrap}
.stat .num{font-size:12.5px;display:flex;align-items:center;gap:4px}
.stat .lbl{font-size:12.5px;font-weight:500;margin-top:10px;letter-spacing:.2px}
.divider{position:absolute;left:73px;top:200px;width:1127px;height:1px;background:#e2e2e2}
.heading{position:absolute;left:108px;top:230px;font-size:21px;font-weight:500;display:flex;align-items:center;gap:8px;white-space:nowrap}
.range{position:absolute;top:294px;width:131px;height:38px;background:var(--btn-grey);color:#333;font-size:12.5px;font-weight:500;display:flex;align-items:center;justify-content:center;gap:4px;box-shadow:0 1px 2px rgba(0,0,0,.15);white-space:nowrap}
.range.on{background:var(--blue);color:#fff}
.chart-card{position:absolute;left:108px;top:360px;width:1053px;height:448px;background:#fff;box-shadow:0 1px 4px rgba(0,0,0,.15)}
.chart-title{position:absolute;left:139px;top:385px;color:var(--blue);font-size:15px;display:flex;align-items:center;gap:6px}
.chart{position:absolute;left:0;top:0;display:block}
.legend{position:absolute;font-size:10.8px;color:#333;display:flex;align-items:center;gap:9px;white-space:nowrap}
.legend i{display:block;width:8px;height:8px}
</style>
</head>
<body>
<div class="canvas">
<header class="topbar">
  <div class="brand"><span class="brand-dot"></span>Domiva</div>
  <span class="nav active" style="left:266px">&#8962; Dashboard</span>
  <span class="nav" style="left:354px">Customers</span>
  <span class="nav" style="left:422px">Properties</span>
  <span class="nav" style="left:487px">Tenants</span>
  <span class="nav" style="left:541px">Contacts</span>
  <span class="nav" style="left:601px">Contractors</span>
  <span class="nav" style="left:672px">Employees</span>
  <span class="nav" style="left:739px">Compliance Management</span>
  <span class="nav" style="left:874px">Prevent Maintenance</span>
  <span class="nav" style="left:988px">More &#8964;</span>
  <div class="avatar" role="img" aria-label="User profile photo"></div>
  <span class="user">Jonah Wexler &#9662;</span>
</header>

<aside class="rail">
  <div class="dock" style="top:51px"><svg width="10" height="10" viewBox="0 0 10 10"><circle cx="4" cy="4" r="3" fill="none" stroke="#555" stroke-width="1.5"/><line x1="6.5" y1="6.5" x2="9" y2="9" stroke="#555" stroke-width="1.5"/></svg></div>
  <div class="dock" style="top:100px"><svg width="10" height="10" viewBox="0 0 10 10"><circle cx="5" cy="5" r="3.5" fill="none" stroke="#555" stroke-width="2" stroke-dasharray="2 1.2"/><circle cx="5" cy="5" r="1.2" fill="#555"/></svg></div>
  <div class="dock" style="top:150px"><svg width="11" height="9" viewBox="0 0 11 9"><rect y="0" width="11" height="2" fill="#555"/><rect y="3.5" width="11" height="2" fill="#555"/><rect y="7" width="11" height="2" fill="#555"/></svg></div>
  <div class="dock" style="top:198px"><svg width="10" height="11" viewBox="0 0 10 11"><path d="M5 1C2.5 1 2 3 2 5v2L1 8h8L8 7V5C8 3 7.5 1 5 1z" fill="#555"/><circle cx="5" cy="9.5" r="1.2" fill="#555"/></svg></div>
  <div class="dock" style="top:248px;font-size:10px;font-weight:500;color:#555">?</div>
  <div class="back"><svg width="20" height="10" viewBox="0 0 20 10"><line x1="2" y1="5" x2="19" y2="5" stroke="#fff" stroke-width="2.5"/><path d="M6 1L2 5l4 4" fill="none" stroke="#fff" stroke-width="2.5"/></svg></div>
</aside>

<section>
  <div class="stat" style="left:108px;width:100px"><div class="num">&#8962; 3</div><div class="lbl">PROPERTIES</div></div>
  <div class="stat" style="left:253px;width:100px"><div class="num">&#9711; 8</div><div class="lbl">TENANTS</div></div>
  <div class="stat" style="left:399px;width:176px"><div class="num">&#10021; 422,000.00 sq.ft</div><div class="lbl">TOTAL PROPERTIES AREA</div></div>
  <div class="stat" style="left:621px;width:138px"><div class="num">&#10021; 233,500.00 sq.ft.</div><div class="lbl">RENTED AREA</div></div>
  <div class="stat" style="left:800px;width:137px"><div class="num">&#10021; 188,500.00 sq.ft.</div><div class="lbl">PROPERTIES</div></div>
</section>
<div class="divider"></div>

<h1 class="heading">&#8962; ACTIVE DASHBOARD</h1>

<div class="range on" style="left:108px">&#9719; LAST 7 DAYS</div>
<div class="range" style="left:280px">&#9719; LAST MONTHS</div>
<div class="range" style="left:453px">&#9719; LAST 3 MONTHS</div>
<div class="range" style="left:625px">&#9719; NEXT 7 DAYS</div>
<div class="range" style="left:798px">&#9719; NEXT MONTHS</div>
<div class="range" style="left:970px">&#9719; NEXT 3 MONTHS</div>

<div class="chart-card"></div>
<div class="chart-title"><svg width="17" height="14" viewBox="0 0 17 14"><rect x="2" y="6" width="2" height="6" fill="#0a7cff"/><rect x="6" y="3" width="2" height="9" fill="#0a7cff"/><rect x="10" y="7" width="2" height="5" fill="#0a7cff"/><rect x="14" y="1" width="2" height="11" fill="#0a7cff"/><rect x="0" y="12.5" width="17" height="1.5" fill="#0a7cff"/></svg>12/27/2020 - 01/03/2021</div>

<svg class="chart" width="1200" height="945" font-family="Roboto, sans-serif" font-size="11.3" fill="#333">
  <g stroke="var(--grid)" stroke-width="1">
    <line x1="176" y1="450" x2="1161" y2="450"/>
    <line x1="176" y1="508" x2="1161" y2="508"/>
    <line x1="176" y1="565" x2="1161" y2="565"/>
    <line x1="176" y1="623" x2="1161" y2="623"/>
    <line x1="176" y1="680" x2="1161" y2="680"/>
    <line x1="176" y1="738" x2="1161" y2="738"/>
  </g>
  <g text-anchor="end">
    <text x="162" y="454">1.25</text>
    <text x="163" y="512">1</text>
    <text x="163" y="569">0.75</text>
    <text x="163" y="627">0.5</text>
    <text x="163" y="684">0.25</text>
    <text x="160" y="742">0</text>
  </g>
  <rect x="555" y="450" width="6" height="58" fill="#000"/>
  <rect x="555" y="508" width="6" height="230" fill="var(--blue)"/>
  <g stroke="#ddd">
    <line x1="295" y1="761" x2="295" y2="777"/><line x1="417" y1="761" x2="417" y2="777"/>
    <line x1="543" y1="761" x2="543" y2="777"/><line x1="664" y1="761" x2="664" y2="777"/>
    <line x1="789" y1="761" x2="789" y2="777"/><line x1="914" y1="761" x2="914" y2="777"/>
    <line x1="1038" y1="761" x2="1038" y2="777"/>
  </g>
  <g text-anchor="middle">
    <text x="234" y="773">27 DEC 2020</text><text x="358" y="773">28 DEC 2020</text>
    <text x="481" y="773">29 DEC 2020</text><text x="605" y="773">30 DEC 2020</text>
    <text x="729" y="773">31 DEC 2020</text><text x="853" y="773">01 JAN 2021</text>
    <text x="976" y="773">02 JAN 2021</text><text x="1101" y="773">03 JAN 2021</text>
  </g>
</svg>

<div class="legend" style="left:112px;top:836px"><i style="background:#7fb6ee"></i>Scheduled Maintenance</div>
<div class="legend" style="left:284px;top:836px"><i style="background:#8fe07a"></i>Completed Scheduled Maintenance</div>
<div class="legend" style="left:512px;top:836px"><i style="background:#f5a04a"></i>Future Scheduled Maintenance</div>
<div class="legend" style="left:715px;top:836px"><i style="background:#444"></i>Scheduled Work Orders</div>
<div class="legend" style="left:883px;top:836px"><i style="background:#8a85ef"></i>Completed Work Orders</div>
<div class="legend" style="left:112px;top:872px"><i style="background:#ef5a7e"></i>Property Inspections in Progress</div>
<div class="legend" style="left:325px;top:872px"><i style="background:#e6cf4a"></i>Completed Property Inspections</div>
</div>
</body>
</html>
```